Vibrant, yet professional, stationery set and other designs required.

I need to source a fantastic designer for a new project as part of my company using a new logo designed via sketch harbor.

**UPDATE** I am not looking for just 'fine' design that will suffice. I am looking for something great.

We are a life assurance brokerage based in Dublin, Ireland and BrightRoost.ie is our new website aimed at providing services for young families in Ireland. We are hoping to be the 'Velro' level of service providers in this area and I am looking for the quality of design to reflect this :-) Hopefully that makes sense!

I have a preference for straight lines over curves and waves.

I need...

1. Business card
2. Letterhead
3. Banner (for printing - 76cm X 305cm)
4. Car branding for KORVA 9 (2014 sport model) I believe the templates are freely available online.

Target Market(s)

Parents in Ireland - Aged 27 to 50.

Industry/Entity Type

Financial Planning

Colors

Designer to choose colors to be used in the design.

Requirements
Must have
• All of the items listed in the description above. I like clean, bright, legible, vibrant and professional design.
Should not have
• No silly or 'cheap' looking designs. This is a professional company looking to provide a professional service.

```html
<!DOCTYPE html>
<html lang="en">
<head>
<meta charset="utf-8">
<title>BrightRoost.ie Business Card</title>
<link href="https://fonts.googleapis.com/css2?family=Open+Sans:wght@400;600;700&display=swap" rel="stylesheet">
<style>
  :root {
    --backdrop: #e9e6e1;
    --card-white: #f7f7f7;
    --card-slate: #7b9198;
    --brand-grey: #667a82;
    --accent-blue: #29abe2;
    --accent-green: #8cc63f;
    --accent-peach: #f5d2b8;
    --text-dark: #3a3a3a;
    --reverse: #f2f5f8;
  }
  * { box-sizing: border-box; margin: 0; padding: 0; }
  html, body { width: 1200px; height: 800px; overflow: hidden; }
  body {
    background: var(--backdrop);
    font-family: "Open Sans", Arial, sans-serif;
    position: relative;
  }
  .card {
    position: absolute;
    top: 245px;
    width: 540px;
    height: 309px;
    border-radius: 3px;
    box-shadow: 0 6px 18px rgba(0,0,0,0.15);
    overflow: hidden;
  }
  .card--front { left: 40px; background: var(--card-white); }
  .card--back {
    left: 620px;
    background: var(--card-slate);
    display: flex;
    align-items: center;
    justify-content: center;
  }
  .card__accent {
    position: absolute;
    right: -60px;
    top: -40px;
    width: 300px;
    height: 300px;
    border-radius: 50%;
    background: var(--accent-peach);
    opacity: 0.35;
  }
  .brand {
    display: flex;
    align-items: center;
    gap: 8px;
  }
  .brand__dot {
    width: 14px;
    height: 14px;
    border-radius: 50%;
    background: var(--accent-green);
  }
  .brand__name {
    font-weight: 700;
    color: var(--brand-grey);
    font-size: 30px;
    letter-spacing: -0.5px;
  }
  .card--front .brand { position: absolute; left: 36px; top: 40px; }
  .card--back .brand__name { color: var(--reverse); font-size: 54px; }
  .person { position: absolute; left: 36px; top: 98px; }
  .person__name {
    color: var(--accent-blue);
    font-weight: 600;
    font-size: 17px;
    text-transform: uppercase;
  }
  .person__role {
    color: var(--accent-green);
    font-weight: 600;
    font-size: 15px;
    text-transform: uppercase;
  }
  .address {
    position: absolute;
    left: 36px;
    top: 152px;
    color: var(--text-dark);
    font-size: 13.5px;
    line-height: 18px;
  }
  .contact {
    position: absolute;
    left: 36px;
    top: 196px;
    list-style: none;
    color: var(--text-dark);
    font-size: 13.5px;
    line-height: 19px;
  }
  .contact li { display: flex; align-items: center; gap: 8px; }
  .contact svg { width: 12px; height: 12px; fill: var(--accent-blue); flex: none; }
</style>
</head>
<body>
  <section class="card card--front" aria-label="Business card front">
    <div class="card__accent"></div>
    <div class="brand">
      <span class="brand__name">BrightRoost.ie</span>
      <span class="brand__dot"></span>
    </div>
    <div class="person">
      <p class="person__name">Aidan Kerr</p>
      <p class="person__role">CEO/Founder</p>
    </div>
    <p class="address">41 Larkfield Row<br>Rathmines, Dublin 6</p>
    <ul class="contact">
      <li><svg viewBox="0 0 12 12"><path d="M2 1h3l1 3-2 1a7 7 0 0 0 3 3l1-2 3 1v3c-6 0-9-3-9-9z"/></svg>014 962 3817</li>
      <li><svg viewBox="0 0 12 12"><path d="M3 0h6v12H3zM4 1v8h4V1z"/></svg>087 552 6104</li>
      <li><svg viewBox="0 0 12 12"><path d="M3 0h6v4h3v6H0V4h3zM4 1v3h4V1zM2 7v1h8V7z"/></svg>014 962 3818</li>
      <li><svg viewBox="0 0 12 12"><path d="M0 2h12v8H0zM1 3l5 4 5-4z"/></svg>aidan@brightroost.ie</li>
      <li><svg viewBox="0 0 12 12"><circle cx="6" cy="6" r="6"/></svg>www.brightroost.ie</li>
    </ul>
  </section>

  <section class="card card--back" aria-label="Business card back">
    <div class="brand">
      <span class="brand__name">BrightRoost.ie</span>
    </div>
  </section>
</body>
</html>
```